Online Dating Website called WinkAtWheel.com

PLEASE CAN ALL PARTICIPATING DESIGNERS PLEASE SUBMIT ALL PAGES AS DETAILED IN THE ORIGINAL BRIEF BELOW WITHIN 48 HOURS TO AVOID WINKATWHEEL EXTENDING THE CONTEST FURTHER.

We have an online dating website that is 95% fully functional and now require an exciting and creative designer to help us create the best dating experience. We are looking for your ideas on a couple of our key pages. These are our landing, profile and search page. We already have a homepage that we are happy with and winning designers will look to build upon the foundations of the homepage and extend them through their designs.

The premise of the site is the idea that if you've ever seen someone out driving and wished you could communicate because you found them attractive, how would you? Well with WinkAtWheel.com you can. Just enter their vehicle registration number (license plate) in to the website in order to get in touch, flirt and develop a relationship. It also allows users to find each other based on other criteria. It acts as both a specialist service and a normal dating website.

The pages that require developing are 1) our landing page, this is the page users see when they first login to the site, it comprises various pieces of information but it's primary function is a live feed of events generated based on the users favourited profiles and interactions with the user. 2) The profile page is the page where users can edit their own information, given the nature of this page we are looking for a creative design that gives this page some flair. 3) Finally we are looking for ideas for our search page, this page needs to provide a list of users who meet the user's search requirements and display the profile of a selected user.
Updates

Project Deadline Extended
Reason: We've asked for certain pages in our brief to be designed and this still hasn't been done. We've contacted the designers that have currently submitted designs and requested this several times. We still await for this to happen.

Target Market(s)

Male or Female age 18+

Industry/Entity Type

Dating

Requirements
Must have
• Our must have feature is a designer with an open mind. The functionality of the site must be present, all we ask is for you to be creative with the layout. Think out side of the box, change the colours, the layout, and the background as you feel. Make it look current and appealing to the user.
Nice to have
• Theme's carried through from the home page
Should not have
• Do not include Comic Sans or Times New Roman font in your designs.

```html
<!DOCTYPE html>
<html lang="en">
<head>
<meta charset="utf-8">
<title>WinkAtWheel.com – Search</title>
<link rel="stylesheet" href="https://fonts.googleapis.com/css2?family=Open+Sans:wght@400;600;700&display=swap">
<style>
:root{
  --nav:#2b2b2b;
  --page-dark:#3a3034;
  --panel:#ffffff;
  --panel-line:#e3e3e3;
  --green:#4f9c1f;
  --green-dark:#3c7d12;
  --purple:#7a2fa8;
  --purple-dark:#5f1f88;
  --pink:#e0287f;
  --pink-dark:#c0196a;
  --blue:#2c7cc4;
  --blue-dark:#1d62a5;
  --label-green:#3f8a17;
  --label-pink:#d8237a;
  --label-blue:#2c7cc4;
  --name-purple:#7a2fa8;
  --text:#333333;
  --muted:#666666;
  --bubble:#e9e9e9;
  --shade:rgba(20,16,18,.58);
}
*{box-sizing:border-box;margin:0;padding:0}
html,body{width:1200px;height:1136px;overflow:hidden;background:var(--page-dark)}
body{font-family:"Open Sans",Arial,sans-serif;color:var(--text)}
.canvas{position:relative;width:1000px;height:947px;transform:scale(1.2);transform-origin:0 0;overflow:hidden}
.backdrop{position:absolute;inset:0;background:
  radial-gradient(ellipse at 80% 40%,#d9b13a 0%,transparent 35%),
  radial-gradient(ellipse at 25% 60%,#c44a3c 0%,transparent 40%),
  radial-gradient(ellipse at 60% 20%,#8a5fb8 0%,transparent 35%),
  linear-gradient(135deg,#6d5a52,#b8907a 45%,#7d6a70)}
.topbar{position:absolute;left:0;top:0;width:1000px;height:45px;background:var(--nav)}
.brand{position:absolute;left:15px;top:11px;display:flex;align-items:center;gap:8px;color:#fff;font-weight:600;font-size:21px;letter-spacing:.5px}
.brand-dot{width:22px;height:22px;border-radius:50%;background:var(--pink)}
.nav{position:absolute;top:16px;font-size:11.5px;color:#cfcfcf}
.nav.right{display:flex;gap:4px;align-items:center}
.panel{position:absolute;background:var(--panel);border-radius:3px;overflow:hidden}
.phead{height:35px;color:#fff;font-weight:700;font-size:16px;display:flex;align-items:center;padding-left:42px;position:relative;text-transform:uppercase}
.phead .ico{position:absolute;left:10px;top:7px;width:22px;height:22px;border-radius:50%;background:rgba(255,255,255,.25)}
.phead.noico{padding-left:11px}
.phead .rico{position:absolute;right:8px;top:7px;width:22px;height:22px;border-radius:50%;background:rgba(255,255,255,.25)}
.green{background:linear-gradient(var(--green),var(--green-dark))}
.purple{background:linear-gradient(var(--purple),var(--purple-dark))}
.pink{background:linear-gradient(var(--pink),var(--pink-dark))}
.blue{background:linear-gradient(var(--blue),var(--blue-dark))}
.settings{font-size:10.5px;padding:10px 12px;line-height:22px}
.settings b{color:var(--label-green);font-weight:700}
.results{padding:0 14px}
.result{position:relative;height:93px;border-bottom:1px solid var(--panel-line);padding-top:8px}
.avatar{position:absolute;left:0;top:10px;width:76px;height:76px;border:1px solid #ccc;padding:3px;background:#fff}
.avatar span{display:block;width:100%;height:100%;background:radial-gradient(circle at 50% 50%,#b8283e 0,#5a1020 40%,#141014 75%)}
.rname{position:absolute;left:105px;top:6px;color:var(--name-purple);font-weight:700;font-size:12.5px}
.rmeta{position:absolute;left:105px;top:23px;font-size:9px;color:var(--muted)}
.ricons{position:absolute;right:4px;top:20px;display:flex;gap:3px}
.ricons i{width:8px;height:8px;background:var(--name-purple);border-radius:2px;display:block}
.bubble{position:absolute;left:105px;top:36px;width:253px;height:45px;background:var(--bubble);border-radius:4px;padding:6px 8px;font-size:8.5px;font-style:italic;color:#555;line-height:14px;overflow:hidden}
.status-text{padding:8px 16px;color:var(--pink);font-weight:700;font-style:italic;font-size:16px}
.bio{padding:10px 13px;font-size:10.5px;line-height:14px}
.bio p{margin-bottom:12px}
.bio b{color:var(--purple-dark)}
.profile-card h3{padding:8px 11px 0;font-size:12px;font-weight:700}
.portrait{margin:8px 15px;width:137px;height:110px;background:radial-gradient(circle at 50% 70%,#f0b238 0,#8a4a20 25%,#1c2a50 60%,#0b1430 100%)}
.tabs{display:flex;gap:3px;padding:0 12px}
.tabs span{font-size:7px;font-weight:700;color:#fff;padding:3px 5px;border-radius:3px}
.about{padding:4px 10px}
.about div{font-size:10.5px;height:25.3px;line-height:25px;border-bottom:1px solid var(--panel-line)}
.about b{color:var(--label-pink);font-weight:700;text-transform:uppercase}
.options div{font-size:10.5px;height:25px;line-height:25px;padding-left:15px;position:relative}
.options div:before{content:"";position:absolute;left:3px;top:9px;width:7px;height:7px;border-radius:50%;background:var(--green)}
.qbox{margin:12px 11px 10px;height:106px;border:1px solid #ccc;border-radius:3px;font-size:10.5px;color:#777;padding:6px}
.send{margin-left:11px;width:63px;height:26px;border-radius:3px;background:var(--blue-dark);color:#fff;font-size:10px;font-weight:700;display:flex;align-items:center;justify-content:center;gap:5px}
.openchat{position:absolute;left:870px;top:921px;width:130px;height:26px;background:#f2f2f2;border-radius:3px 0 0 0;font-size:12px;font-weight:700;display:flex;align-items:center;justify-content:center;gap:8px;color:#222}
.shade{position:absolute;inset:0;background:var(--shade)}
.modal{position:absolute;left:278px;top:125px;width:439px;height:336px;background:#fff;border-radius:3px}
.modal-head{height:38px;background:linear-gradient(var(--pink),var(--pink-dark));color:#fff;font-weight:700;font-size:16px;line-height:38px;padding-left:13px}
.close{position:absolute;left:425px;top:-8px;width:20px;height:20px;border-radius:50%;background:#111;border:2px solid #fff}
.col{position:absolute;top:60px}
.check{display:flex;align-items:center;gap:7px;font-size:11.5px;font-weight:600;color:#111;margin-bottom:19px}
.box{width:14px;height:14px;background:#e8e8e8;border:1px solid #d8d8d8}
.field{height:47.5px}
.field .k{color:var(--label-blue);font-weight:700;font-size:10.5px;line-height:14px}
.field .v{font-size:10.5px;color:#444;line-height:18px}
</style>
</head>
<body>
<div class="canvas">
  <div class="backdrop" role="img" aria-label="Blurred colourful photographic backdrop"></div>

  <header class="topbar">
    <div class="brand"><span>WINKATWHEEL</span><span class="brand-dot"></span></div>
    <span class="nav" style="left:210px">Home</span>
    <span class="nav" style="left:265px">Profile</span>
    <span class="nav" style="left:320px">Message</span>
    <span class="nav" style="left:388px">Matches</span>
    <span class="nav" style="left:455px">Search</span>
    <span class="nav" style="left:843px">Support</span>
    <span class="nav" style="left:910px">My Account</span>
  </header>

  <section class="panel" style="left:15px;top:65px;width:372px;height:123px">
    <div class="phead green"><span class="ico"></span>Search Settings</div>
    <div class="settings">
      <div><b>Looking for:</b> Both <span style="position:absolute;left:272px">Advanced Search</span></div>
      <div><b>Minimum Age:</b> 18 &nbsp;&nbsp;&nbsp;&nbsp;&nbsp;&nbsp;&nbsp; <b>Maximum Age:</b> 99</div>
      <div><b>Distance:</b> Any Distance</div>
    </div>
  </section>

  <section class="panel" style="left:15px;top:205px;width:372px;height:607px">
    <div class="phead purple"><span class="ico"></span>My Results</div>
    <div class="results">
      <div class="result"><div class="avatar" role="img" aria-label="Member profile photo"><span></span></div><div class="rname">STUPID LLAMA</div><div class="rmeta">24 years old - from brindlemoor</div><div class="bubble">Lorem Ipsum is simply dummy text of the typesetting industry. Lorem Ipsum has been the industry's</div></div>
      <div class="result"><div class="avatar" role="img" aria-label="Member profile photo"><span></span></div><div class="rname">STUPID LLAMA</div><div class="rmeta">24 years old - from brindlemoor</div><div class="bubble">Lorem Ipsum is simply dummy text of the typesetting industry. Lorem Ipsum has been the industry's</div></div>
      <div class="result"><div class="avatar" role="img" aria-label="Member profile photo"><span></span></div><div class="rname">STUPID LLAMA</div><div class="rmeta">24 years old - from brindlemoor</div><div class="ricons"><i></i><i></i><i></i><i></i></div><div class="bubble">Lorem Ipsum is simply dummy text of the typesetting industry. Lorem Ipsum has been the industry's</div></div>
      <div class="result"><div class="avatar" role="img" aria-label="Member profile photo"><span></span></div><div class="rname">STUPID LLAMA</div><div class="rmeta">24 years old - from brindlemoor</div><div class="ricons"><i></i><i></i><i></i><i></i></div><div class="bubble">Lorem Ipsum is simply dummy text of the typesetting industry. Lorem Ipsum has been the industry's</div></div>
      <div class="result"><div class="avatar" role="img" aria-label="Member profile photo"><span></span></div><div class="rname">STUPID LLAMA</div><div class="rmeta">24 years old - from brindlemoor</div><div class="ricons"><i></i><i></i><i></i><i></i></div><div class="bubble">Lorem Ipsum is simply dummy text of the typesetting industry. Lorem Ipsum has been the industry's</div></div>
      <div class="result" style="border:0"><div class="avatar" role="img" aria-label="Member profile photo"><span></span></div><div class="rname">STUPID LLAMA</div><div class="rmeta">24 years old - from brindlemoor</div><div class="ricons"><i></i><i></i><i></i><i></i></div><div class="bubble">Lorem Ipsum is simply dummy text of the typesetting industry. Lorem Ipsum has been the industry's</div></div>
    </div>
  </section>

  <section class="panel" style="left:402px;top:65px;width:372px;height:72px">
    <div class="phead pink"><span class="ico"></span>Status</div>
    <div class="status-text">“OK”</div>
  </section>

  <section class="panel" style="left:402px;top:153px;width:372px;height:78px">
    <div class="phead blue"><span class="ico"></span>Vehicle</div>
  </section>

  <section class="panel" style="left:402px;top:245px;width:372px;height:165px">
    <div class="phead green"><span class="ico"></span>Looking For</div>
    <div class="bio"><p>Lorem Ipsum is simply dummy text of the printing and typesetting industry. Lorem Ipsum has been the industry's standard dummy text ever since the 1500s, when an unknown printer took a galley of type and scrambled it. It has survived not only five centuries, but also the leap into electronic typesetting. It was popularised with the release</p></div>
  </section>

  <section class="panel" style="left:402px;top:425px;width:372px;height:465px">
    <div class="phead purple"><span class="ico"></span>About Me</div>
    <div class="bio">
      <p><b>MOVIES:</b> Lorem Ipsum is simply dummy text of the printing and typesetting industry.</p>
      <p><b>TV:</b> Lorem Ipsum is simply dummy text of the printing and typesetting industry. Lorem Ipsum has been the industry's standard dummy text ever since the 1500s, when an unknown printer took a galley of type and scrambled it to make a type specimen book. It has survived not only five centuries, but also the leap into electronic typesetting, remaining essentially unchanged.</p>
      <p style="margin-top:20px"><b>MUSIC:</b> Lorem Ipsum is simply dummy text of the printing and typesetting industry</p>
      <p><b>PETS:</b> Lorem Ipsum is simply dummy text of the printing</p>
      <p><b>LANGUAGES:</b> Lorem Ipsum is simply dummy text</p>
      <p><b>INTERESTS:</b> Lorem Ipsum is simply dummy text of the printing and typesetting industry. Lorem Ipsum has been the industry's standard dummy text ever since the 1500s, when an unknown printer took a galley of type and scrambled it to make a type specimen book. It has survived not only five centuries, but also the leap into electronic typesetting, remaining essentially unchanged.</p>
      <p><b>HOBBIES:</b> It was popularised in the 1960s with the release of Typeline sheets containing Lorem Ipsum passages, and more recently with desktop publishing software like PageForge Studio including versions of Lorem Ipsum.</p>
    </div>
  </section>

  <section class="panel profile-card" style="left:789px;top:65px;width:197px;height:220px">
    <div class="phead blue noico">Dion</div>
    <h3>(33 years old - brindlemoor)</h3>
    <div class="portrait" role="img" aria-label="Dion's profile picture: a figure silhouetted against a glowing sunset"></div>
    <div class="tabs"><span class="pink">PROFILE</span><span class="green">GALLERY</span><span class="blue">ACTIVITY</span></div>
  </section>

  <section class="panel" style="left:789px;top:293px;width:197px;height:242px">
    <div class="phead pink noico">About Dion<span class="rico"></span></div>
    <div class="about">
      <div><b>Eye color:</b> Gray</div>
      <div><b>Hair color:</b> Grey &amp; White</div>
      <div><b>Height:</b> 6'6"</div>
      <div><b>Body:</b> Average</div>
      <div><b>Smoking:</b> No</div>
      <div><b>Drinking:</b> Sometimes</div>
      <div><b>Children:</b> Has children</div>
      <div style="border:0"><b>Education:</b> College</div>
    </div>
  </section>

  <section class="panel options" style="left:789px;top:550px;width:197px;height:120px">
    <div class="phead green noico">Options<span class="rico"></span></div>
    <div style="padding-top:4px">
      <div>Unfavourite Dion</div>
      <div>Chat with Dion</div>
      <div>Go to Search</div>
    </div>
  </section>

  <section class="panel" style="left:789px;top:685px;width:197px;height:205px">
    <div class="phead pink noico">Quick Message<span class="rico"></span></div>
    <div class="qbox">Type your message to Dion:</div>
    <div class="send">
      <svg width="10" height="8" viewBox="0 0 10 8"><path d="M0 4h8M5 1l3 3-3 3" stroke="#fff" stroke-width="1.5" fill="none"/></svg>SEND
    </div>
  </section>

  <div class="openchat">
    <svg width="13" height="11" viewBox="0 0 13 11"><path d="M0 0h13v8H4l-3 3V8H0z" fill="#222"/></svg>OPEN CHAT
  </div>

  <div class="shade"></div>

  <div class="modal">
    <div class="modal-head">ADVANCED SEARCH SETTINGS</div>
    <div class="close">
      <svg width="16" height="16" viewBox="0 0 16 16"><path d="M5 5l6 6M11 5l-6 6" stroke="#fff" stroke-width="1.3"/></svg>
    </div>
    <div class="col" style="left:23px">
      <div class="check"><span class="box"><svg width="12" height="12" viewBox="0 0 12 12"><path d="M2 6l3 3 6-7" stroke="#555" stroke-width="1.6" fill="none"/></svg></span>APPEAREANCES</div>
      <div class="field"><div class="k">Eye Colour:</div><div class="v">No preference</div></div>
      <div class="field"><div class="k">Hair Colour:</div><div class="v">No preference</div></div>
      <div class="field"><div class="k">Minium Height:</div><div class="v">0' 0"</div></div>
      <div class="field"><div class="k">Maximum Height:</div><div class="v">8' 0"</div></div>
      <div class="field"><div class="k">Body Type:</div><div class="v">No preference</div></div>
    </div>
    <div class="col" style="left:188px">
      <div class="check"><span class="box"><svg width="12" height="12" viewBox="0 0 12 12"><path d="M2 6l3 3 6-7" stroke="#555" stroke-width="1.6" fill="none"/></svg></span>LIFESTYLE</div>
      <div class="field"><div class="k">Smoker:</div><div class="v">No preference</div></div>
      <div class="field"><div class="k">Drinker</div><div class="v">No preference</div></div>
      <div class="field"><div class="k">Education:</div><div class="v">No preference</div></div>
      <div class="field"><div class="k">Has Children:</div><div class="v">No preference</div></div>
    </div>
    <div class="col" style="left:320px">
      <div class="check"><span class="box"></span>VEHICLE</div>
      <div class="field"><div class="k">Make:</div><div class="v">Kestrel</div></div>
      <div class="field"><div class="k">Model:</div><div class="v">Lumara</div></div>
      <div class="field"><div class="k">Colour:</div><div class="v">Colour</div></div>
    </div>
  </div>
</div>
</body>
</html>
```